Marlowby Services Website Design

We have most content but require a professional design. We have a logo already and will need it utilized along with several of the photos from the attached documentation.
First page should have our mission and Vision and the synapsis provided in the word document. Visitors will be prompted to select from one of our 3 divisions from this page.
Each division will have the same list of tabs : About, Services, Safety, Careers and Contact.
Photos on each divisions page should be representative of the divisions offerings. The word doc attached contains the requested content and we are open to edits that would complement and fill the website.
I like the Quorvane site www.quorvane.example - they are our competition so cant be modeled directly after this.
Please include prompts to request quote at each service page. align the format of the geotechnical page to the other 2 divisions.
I used chat gpt for some of the content so will need it optimized for SCO.

```html
<!DOCTYPE html>
<html lang="en">
<head>
<meta charset="UTF-8">
<title>Marlowby Services</title>
<link href="https://fonts.googleapis.com/css2?family=Poppins:wght@600;700;800;900&family=Mulish:wght@400;500;600&display=swap" rel="stylesheet">
<style>
:root{
  --red:#e3161f;
  --white:#ffffff;
  --ink:#111111;
  --dark:#0e1317;
  --footer:#121212;
  --blue-top:#0a5a96;
  --blue-mid:#2a6fa3;
  --sunset:#d79a62;
  --soft-grey:#eeeeee;
}
*{margin:0;padding:0;box-sizing:border-box}
html,body{width:1200px;height:2687px;overflow:hidden}
body{font-family:'Mulish',sans-serif;color:var(--ink);background:var(--white);position:relative}

/* Hero */
.hero{position:absolute;left:0;top:0;width:1200px;height:665px;overflow:hidden}
.hero-photo{position:absolute;inset:0;background:
  linear-gradient(180deg,#5d7aa0 0%,#8ea1b4 6%,#3e4a2e 14%,#6b5a45 30%,#7a6450 60%,#5e4c3a 100%)}
.hero-truck{position:absolute;left:90px;top:170px;width:980px;height:320px;
  background:
    radial-gradient(ellipse 50% 38% at 55% 30%,rgba(240,240,240,.85) 0%,rgba(220,220,220,.55) 55%,rgba(220,220,220,0) 100%),
    radial-gradient(ellipse 48% 30% at 50% 78%,rgba(30,30,30,.7) 0%,rgba(30,30,30,.35) 55%,rgba(30,30,30,0) 100%)}
.hero-glow{position:absolute;left:0;top:470px;width:1200px;height:195px;
  background:linear-gradient(180deg,rgba(70,55,40,0) 0%,rgba(70,55,40,.35) 100%)}
.logo{position:absolute;font-family:'Poppins',sans-serif;font-weight:800;color:var(--red);letter-spacing:4px}
.hero .logo{left:133px;top:16px;font-size:36px}
.nav{position:absolute;top:27px;left:558px;display:flex;align-items:center;height:35px}
.nav a{color:var(--white);text-decoration:none;font-size:15px;font-family:'Mulish',sans-serif}
.nav .home{background:var(--red);border-radius:18px;padding:0 14px;height:35px;line-height:35px}
.nav .about{margin-left:20px}
.nav .services{margin-left:42px}
.nav .careers{margin-left:45px}
.nav .contact{margin-left:42px}
.vision{position:absolute;left:0;top:512px;width:1200px;text-align:center;color:var(--white)}
.vision h1{font-family:'Poppins',sans-serif;font-weight:900;font-size:46px;letter-spacing:4px;line-height:56px}
.vision p{font-size:18px;line-height:26px;margin-top:10px}

/* Services intro */
.intro{position:absolute;left:0;top:665px;width:1200px;height:627px;overflow:hidden;background:var(--soft-grey)}
.intro-photo{position:absolute;inset:0;background:
  linear-gradient(90deg,#f4f4f4 0%,#e9e9e9 45%,#cfcfcf 70%,#a8826a 82%,#b9b9b9 100%)}
.intro h2{position:absolute;left:157px;top:60px;font-size:34px;line-height:42px;font-family:'Poppins',sans-serif;font-weight:900;letter-spacing:-.5px}
.red-rule{position:absolute;height:3px;background:var(--red)}
.intro .red-rule{left:158px;top:170px;width:53px}
.intro p{position:absolute;left:158px;top:208px;width:365px;font-size:20px;line-height:30.5px}
.btn{position:absolute;left:157px;top:362px;width:138px;height:46px;border-radius:23px;background:var(--red);
  color:var(--white);font-family:'Poppins',sans-serif;font-weight:700;font-size:15px;line-height:46px;text-align:center;text-decoration:none}

/* Mission */
.mission{position:absolute;left:0;top:1292px;width:1200px;height:553px;overflow:hidden}
.mission-photo{position:absolute;inset:0;background:
  linear-gradient(180deg,var(--blue-top) 0%,var(--blue-mid) 35%,#5b7fa0 55%,var(--sunset) 75%,#3a4a2a 92%,#1c2a1a 100%)}
.mission-box{position:absolute;left:173px;top:52px;width:347px;height:158px;border:1px solid rgba(255,255,255,.75);
  display:flex;align-items:center;justify-content:center;text-align:center}
.mission-box h2{color:var(--white);font-family:'Poppins',sans-serif;font-weight:900;font-size:34px;line-height:47px;letter-spacing:-.5px}
.mission p{position:absolute;left:567px;top:48px;width:492px;color:var(--white);font-size:15px;line-height:20.8px}

/* Divisions */
.division-head{position:absolute;left:0;top:1845px;width:1200px;height:156px;background:var(--dark);text-align:center}
.division-head h2{color:var(--white);font-family:'Poppins',sans-serif;font-weight:900;font-size:34px;letter-spacing:-.5px;margin-top:38px}
.division-head .red-rule{left:573px;top:106px;width:54px}
.divisions{position:absolute;left:0;top:2001px;width:1200px;height:431px;display:flex}
.division{position:relative;height:431px;overflow:hidden}
.division.aerial{width:394px;background:linear-gradient(180deg,#9fb38a 0%,#4f6a3c 35%,#d8d8d8 52%,#59544c 70%,#2e2a26 100%)}
.division.drilling{width:405px;background:linear-gradient(180deg,#6c5848 0%,#7a5c48 40%,#5a4436 75%,#2c2420 100%)}
.division.renewable{width:401px;background:linear-gradient(160deg,#1d5fb0 0%,#2f78d0 45%,#6aa0e0 75%,#23508f 100%)}
.division-label{position:absolute;left:34px;bottom:0;width:calc(100% - 68px);height:95px}
.division-label .bar{position:absolute;left:0;top:0;width:78px;height:3px;background:var(--white)}
.division.aerial .division-label .bar{top:18px}
.division-label h3{position:absolute;left:0;bottom:24px;color:var(--white);font-family:'Poppins',sans-serif;font-weight:600;font-size:20px;line-height:25px}
.division-label .arrow{position:absolute;right:0;bottom:25px;width:42px;height:42px;border-radius:10px;background:var(--red)}
.division.drilling .division-label,.division.renewable .division-label{left:38px;width:calc(100% - 58px)}

/* Footer */
.footer{position:absolute;left:0;top:2432px;width:1200px;height:255px;background:var(--footer);text-align:center}
.footer .logo{position:static;display:block;margin-top:52px;font-size:34px;line-height:40px}
.footer-nav{display:flex;justify-content:center;gap:38px;margin-top:30px}
.footer-nav a{color:var(--white);text-decoration:none;font-size:15px}
.footer small{display:block;color:#d6d6d6;font-size:13px;margin-top:36px}
</style>
</head>
<body>

<header class="hero">
  <div class="hero-photo" role="img" aria-label="Aerial view of a dirt lot beside a green-roofed building and tree line"></div>
  <div class="hero-truck" role="img" aria-label="White aerial lift truck with extended boom parked on the lot"></div>
  <div class="hero-glow"></div>
  <div class="logo">MARLOWBY</div>
  <nav class="nav">
    <a class="home" href="#">HOME</a>
    <a class="about" href="#">ABOUT</a>
    <a class="services" href="#">SERVICES</a>
    <a class="careers" href="#">CAREERS</a>
    <a class="contact" href="#">CONTACT</a>
  </nav>
  <div class="vision">
    <h1>OUR VISION</h1>
    <p>To be the leading provider of aerial access, geotechnical drilling, and service solutions, setting<br>the standard for excellence in safety, efficiency, and environmental stewardship.</p>
  </div>
</header>

<section class="intro">
  <div class="intro-photo" role="img" aria-label="Worker in a hard hat blended with a refinery skyline"></div>
  <h2>MARLOWBY<br>SERVICES</h2>
  <div class="red-rule"></div>
  <p>Delivering safe, reliable aerial access and maintenance services to Oil &amp; Gas, Construction, Utility, &amp; Renewable energy industries.</p>
  <a class="btn" href="#">READ MORE</a>
</section>

<section class="mission">
  <div class="mission-photo" role="img" aria-label="Oil refinery towers lit at dusk under a blue sky"></div>
  <div class="mission-box"><h2>MISSION<br>STATEMENT</h2></div>
  <p>At Marlowby, our mission is to deliver unparalleled aerial access, geotechnical drilling, and service and maintenance solutions, consistently exceeding our clients' expectations. We strive to achieve this by investing in cutting-edge technology, fostering a culture of safety and continuous improvement, and prioritizing environmental sustainability. Through collaboration, integrity, and dedication, we aim to contribute to the success of our clients while maintaining the highest standards of quality and professionalism.</p>
</section>

<section class="division-head">
  <h2>SELECT DIVISION</h2>
  <div class="red-rule"></div>
</section>

<section class="divisions">
  <article class="division aerial" role="img" aria-label="Boom lift truck on a gravel road in a forest">
    <div class="division-label">
      <div class="bar"></div>
      <h3>AERIAL ACCESS</h3>
      <span class="arrow"><svg width="42" height="42" viewBox="0 0 42 42"><path d="M17 11 L27 21 L17 31" fill="none" stroke="#fff" stroke-width="2.5" stroke-linecap="round" stroke-linejoin="round"/></svg></span>
    </div>
  </article>
  <article class="division drilling" role="img" aria-label="Aerial view of a drilling rig on a muddy construction site">
    <div class="division-label">
      <div class="bar"></div>
      <h3>GEOTECHNICAL<br>DRILLING</h3>
      <span class="arrow"><svg width="42" height="42" viewBox="0 0 42 42"><path d="M17 11 L27 21 L17 31" fill="none" stroke="#fff" stroke-width="2.5" stroke-linecap="round" stroke-linejoin="round"/></svg></span>
    </div>
  </article>
  <article class="division renewable" role="img" aria-label="Wind turbine blades against a blue sky">
    <div class="division-label">
      <div class="bar"></div>
      <h3>RENEWABLE ENERGY<br>SERVICES</h3>
      <span class="arrow"><svg width="42" height="42" viewBox="0 0 42 42"><path d="M17 11 L27 21 L17 31" fill="none" stroke="#fff" stroke-width="2.5" stroke-linecap="round" stroke-linejoin="round"/></svg></span>
    </div>
  </article>
</section>

<footer class="footer">
  <span class="logo">MARLOWBY</span>
  <nav class="footer-nav">
    <a href="#">HOME</a>
    <a href="#">ABOUT</a>
    <a href="#">SERVICES</a>
    <a href="#">CAREERS</a>
    <a href="#">CONTACT</a>
  </nav>
  <small>Copyright © 2024 All Rights Reserved</small>
</footer>

</body>
</html>
```